FinTech company looking to revamp and expand client-facing interface for our financial models

Pellworth Engines currently has a very simple website that allows clients to interact with our financial models. We are looking to completely redesign the current site and add several extra pages to provide extra functionality. We want the design to have a modern, slick feel, that will work on both a desktop or a tablet. It should be straightforward for clients to move between different pages at any time, and clear from the layout how to interact with the more advanced features. We have included screenshots of existing pages in the attached design brief, as well as sketches of the functionality required by the new pages, but can't provide a direct link to the current site.
Target Market(s)
Professional investors that will be paying to access the interface
Industry/Entity Type
Finance
Number of Pages Required
4 page
Colors
Designer to choose colors to be used in the design.
Look and feel
Each slider illustrates characteristics of the customer's brand and the style your logo design should communicate.

```html
<!DOCTYPE html>
<html lang="en">
<head>
<meta charset="utf-8">
<title>QVANTA – Models</title>
<link rel="stylesheet" href="https://fonts.googleapis.com/css2?family=Open+Sans:wght@400;600;700&display=swap">
<style>
:root{
  --teal:#006d6a;
  --white:#ffffff;
  --ink:#111111;
  --page:#404040;
  --tab-dim:#464646;
  --tab-raised:#4a4a4a;
  --tab-text:#2a2a2a;
  --head-dim:#1d4c4a;
  --head-text:#3f7775;
  --row-dim:#3a3a3a;
  --row-line:#444444;
  --cell-text:#1a1a1a;
  --panel:#d3d3d3;
  --line:#e2e2e2;
  --navy:#0f2f57;
}
*{box-sizing:border-box;margin:0;padding:0}
html,body{width:1200px;height:678px;overflow:hidden}
body{font-family:"Open Sans",sans-serif;background:var(--page);position:relative;color:var(--ink)}

.topbar{position:absolute;left:0;top:0;width:1200px;height:55px;background:var(--white)}
.brand{position:absolute;left:66px;top:0;line-height:55px;font-weight:700;font-size:18px;letter-spacing:.3px}
.nav-item{position:absolute;top:0;height:55px;display:flex;align-items:center;justify-content:center;gap:8px;font-weight:600;font-size:13.5px;border-right:1px solid #e6e6e6}
.nav-item.active{background:var(--teal);color:var(--white)}
.nav-item svg{width:22px;height:22px}

.tabs .tab{position:absolute;top:112px;height:32px;background:var(--tab-dim);color:var(--tab-text);font-weight:700;font-size:12.5px;display:flex;align-items:center;justify-content:center}
.tabs .tab.current{top:92px;height:51px;background:var(--tab-raised);align-items:flex-start;padding-top:20px}
.tab-arrow,.tab-add{position:absolute;top:114px;color:#2a2a2a}

.export{position:absolute;left:1084px;top:182px;display:flex;align-items:center;gap:6px;color:#2e2e2e;font-weight:700;font-size:16px}

.models-table{position:absolute;left:97px;top:217px;width:1071px}
.thead{height:65px;background:var(--head-dim);position:relative}
.thead span{position:absolute;top:0;line-height:65px;color:var(--head-text);font-weight:700;font-size:15.5px;padding-left:12px;height:65px;border-left:1px solid #245856}
.row{height:63px;background:var(--row-dim);border-bottom:1px solid var(--row-line);position:relative;color:var(--cell-text);font-size:15.5px}
.row span{position:absolute;top:0;height:63px;display:flex;align-items:center;line-height:22px}

.filters{position:absolute;left:0;top:217px;width:369px;height:212px;background:var(--panel);border-radius:0 6px 6px 0}
.filters-card{position:absolute;left:14px;top:14px;width:341px;height:184px;background:var(--white);border-radius:4px;overflow:hidden}
.filters-title{height:46px;background:var(--teal);color:var(--white);font-weight:700;font-size:17px;text-align:center;line-height:46px}
.filter-row{height:48px;border-bottom:1px solid var(--line);display:flex;align-items:center;padding-left:15px;font-size:15.5px}
.filter-row .label{width:80px}
.filter-row b{width:94px;font-weight:700}
.filter-row .field{width:139px;height:30px;border:1px solid #c7c7c7;border-radius:4px;padding-left:11px;line-height:28px}
.apply{display:flex;align-items:center;gap:9px;padding:9px 0 0 13px;font-weight:700;font-size:15.5px}
.apply .box{width:18px;height:18px;border:1px solid #aaa;border-radius:3px;background:#f2f2f2}
.filters-handle{position:absolute;left:369px;top:235px;width:46px;height:176px;background:var(--panel);border-radius:0 6px 6px 0}
.filters-handle .label{position:absolute;left:4px;top:88px;transform:rotate(-90deg);transform-origin:left top;font-weight:700;font-size:15px;letter-spacing:1.3px;white-space:nowrap;margin-top:0;left:5px;top:122px}
.filters-handle svg{position:absolute;left:30px;top:76px}
</style>
</head>
<body>
<header class="topbar">
  <div class="brand">QVANTA</div>
  <div class="nav-item active" style="left:180px;width:83px">250D</div>
  <div class="nav-item" style="left:263px;width:83px">83D</div>
  <div class="nav-item" style="left:346px;width:83px">42D</div>
  <div class="nav-item active" style="left:554px;width:130px">
    <svg viewBox="0 0 24 24" fill="none" stroke="#fff" stroke-width="2"><path d="M3 11 12 3l9 8"/><path d="M5 10v10h5v-6h4v6h5V10"/></svg>MODELS</div>
  <div class="nav-item" style="left:684px;width:163px">
    <svg viewBox="0 0 24 24" fill="none" stroke="#111" stroke-width="1.4"><circle cx="12" cy="12" r="3"/><circle cx="12" cy="12" r="7" stroke-dasharray="2 2"/><circle cx="12" cy="12" r="10" stroke-dasharray="1.5 2.5"/></svg>SENSITIVITIES</div>
  <div class="nav-item" style="left:847px;width:150px">
    <svg viewBox="0 0 24 24" fill="none" stroke="#111" stroke-width="1.6"><circle cx="7" cy="7" r="4"/><circle cx="17" cy="7" r="4"/><circle cx="7" cy="17" r="4"/><circle cx="17" cy="17" r="4"/></svg>PORTFOLIO</div>
  <div class="nav-item" style="left:997px;width:138px">
    <svg viewBox="0 0 24 24" fill="none" stroke="#111" stroke-width="1.6"><rect x="2" y="3" width="20" height="18"/><path d="M5 16l4-5 3 3 3-5 4 4"/></svg>BACKTEST</div>
</header>

<nav class="tabs">
  <div class="tab" style="left:65px;width:143px">EQUITIES</div>
  <div class="tab" style="left:210px;width:148px">ETFS</div>
  <div class="tab" style="left:360px;width:146px">PAIRS</div>
  <div class="tab current" style="left:508px;width:143px">ETF PAIRS</div>
  <div class="tab" style="left:655px;width:143px">FACTORS</div>
  <div class="tab" style="left:803px;width:143px">NEW TAB TITLE #1</div>
  <div class="tab" style="left:951px;width:143px">NEW TAB TITLE #2</div>
  <svg class="tab-arrow" style="left:1110px" width="14" height="26" viewBox="0 0 14 26"><path d="M3 5l8 8-8 8" fill="none" stroke="#2a2a2a" stroke-width="2.5"/></svg>
  <svg class="tab-add" style="left:1147px" width="24" height="26" viewBox="0 0 24 26"><circle cx="12" cy="13" r="10" fill="none" stroke="#2a2a2a" stroke-width="1.6"/><path d="M12 7v12M6 13h12" stroke="#2a2a2a" stroke-width="1.6"/></svg>
</nav>

<div class="export">
  <svg width="26" height="22" viewBox="0 0 26 22" fill="none" stroke="#2e2e2e" stroke-width="2"><path d="M18 12v8H2V6h6"/><path d="M12 12c0-5 4-8 10-8"/><path d="M18 1l4 3-4 3"/></svg>Export
</div>

<div class="models-table">
  <div class="thead">
    <span style="left:328px;width:83px">Quality</span>
    <span style="left:411px;width:83px">Stat 1</span>
    <span style="left:494px;width:83px">Stat 2</span>
    <span style="left:577px;width:83px">Stat 3</span>
    <span style="left:660px;width:83px">Stat 4</span>
    <span style="left:743px;width:83px">Stat 5</span>
    <span style="left:826px;width:83px">Stat 6</span>
    <span style="left:909px;width:83px">Stat 7</span>
    <span style="left:992px;width:79px">Stat 8</span>
  </div>
  <div class="row"><span style="left:16px">Model 1</span><span style="left:110px">Financials</span><span style="left:228px">2019-07-03<br>12:15:00.000</span><span style="left:338px">30.2288</span><span style="left:411px">2.01574</span><span style="left:508px">23.305</span><span style="left:581px">-0.149368</span><span style="left:668px">22.3054</span><span style="left:752px">4.63714</span><span style="left:827px">0.945706</span><span style="left:909px">2.81949</span><span style="left:1001px">2.60858</span></div>
  <div class="row"><span style="left:16px">Model 2</span><span style="left:110px">Energy</span><span style="left:228px">2019-07-03<br>12:15:00.000</span><span style="left:338px">32.8694</span><span style="left:411px">0.87307</span><span style="left:508px">32.185</span><span style="left:581px">-0.033692</span><span style="left:668px">33.9911</span><span style="left:752px">11.5693</span><span style="left:827px">-0.472968</span><span style="left:909px">-0.830458</span><span style="left:1001px">6.80646</span></div>
  <div class="row"><span style="left:16px">Model 3</span><span style="left:110px">Consumer<br>Discretionary</span><span style="left:228px">2019-07-03<br>12:15:00.000</span><span style="left:338px">1.66002</span><span style="left:411px">-0.569222</span><span style="left:508px">159.814</span><span style="left:581px">0.0252328</span><span style="left:668px">172.616</span><span style="left:752px">10.2875</span><span style="left:827px">-0.750396</span><span style="left:909px">-0.385309</span><span style="left:1001px">4.69146</span></div>
  <div class="row"><span style="left:16px">Model 4</span><span style="left:110px">Information<br>Technology</span><span style="left:228px">2019-07-03<br>12:15:00.000</span><span style="left:338px">45.6856</span><span style="left:411px">0.412148</span><span style="left:508px">202.488</span><span style="left:581px">0.0084923</span><span style="left:668px">205.834</span><span style="left:752px">11.9094</span><span style="left:827px">-0.137913</span><span style="left:909px">0.449595</span><span style="left:1001px">3.85106</span></div>
  <div class="row"><span style="left:16px">Model 5</span><span style="left:110px">Information<br>Technology</span><span style="left:228px">2019-07-03<br>12:15:00.000</span><span style="left:338px">75.7733</span><span style="left:411px">7.06728</span><span style="left:508px">188.605</span><span style="left:581px">0.016913</span><span style="left:668px">161.665</span><span style="left:752px">3.82241</span><span style="left:827px">0.981019</span><span style="left:909px">1.29847</span><span style="left:1001px">3.34927</span></div>
</div>

<aside class="filters">
  <div class="filters-card">
    <div class="filters-title">Filters</div>
    <div class="filter-row"><span class="label">Quality</span><b>Threshold:</b><span class="field">-10</span></div>
    <div class="filter-row"><span class="label"><b style="width:auto">Abs.</b> Stat</span><b>Threshold:</b><span class="field">-10</span></div>
    <div class="apply"><span class="box"></span>Apply to all tabs</div>
  </div>
</aside>
<div class="filters-handle">
  <span class="label">FILTERS</span>
  <svg width="28" height="28" viewBox="0 0 28 28"><circle cx="14" cy="14" r="13" fill="var(--navy)" stroke="#fff" stroke-width="2"/><path d="M19 14H9m4-4-4 4 4 4" fill="none" stroke="#fff" stroke-width="2"/></svg>
</div>
</body>
</html>
```